Consulting Company PowerPoint Template Design

We are looking for an updated PowerPoint template design or our 55 person energy consulting firm (K7) based in San Francisco (www.kseven-example.com). We would like two versions of the same PowerPoint template in a 16:9 and 4:3 format with our existing logo.

We have an existing color scheme and template and are seeking your help to polish/update the template design for wide format and create a flexible template that is easy to use with content from Excel and Word. Our current template, and a couple of examples that we like are attached.

Specific requests include:

• Dark background for slide title
• A narrow section header
• Maximizing white space for content
• A limited number of well designed Master template layouts to choose from
• A selection of title and section header slides that are not San Francisco specific with some variety to chose from ideally with a focus on energy or nature, graphics/visuals.

For examples of energy specific templates see:
https://www.brightslidehub.example/energy/powerpoint-templates/0.html

Requirements
Must have
• Must use our logo but open to other designs, fonts, and styles for the PowerPoint template.
• Please use our existing color scheme found in the attached Excel file.
• Also we would like the ability to easily copy and paste from our existing/original template to the new template. In other words we would like backward compatibility to apply the new template format to our old PowerPoints that use our existing template.

```html
<!DOCTYPE html>
<html lang="en">
<head>
<meta charset="utf-8">
<title>K7 Presentation Template</title>
<link rel="stylesheet" href="https://fonts.googleapis.com/css2?family=Montserrat:wght@300;400;600;700&display=swap">
<style>
  :root {
    --navy: #1c4a69;
    --navy-soft: #2a5f82;
    --gold: #c9a063;
    --ink: #2d3d4a;
    --muted: #7b8791;
    --line: #d9dee2;
    --paper: #ffffff;
    --canvas: #f3f4f5;
  }
  * { box-sizing: border-box; margin: 0; padding: 0; }
  html, body { width: 831px; height: 1200px; overflow: hidden; }
  body {
    background: var(--canvas);
    font-family: "Montserrat", Arial, sans-serif;
    color: var(--ink);
    position: relative;
  }
  .slide {
    position: absolute;
    width: 363px;
    height: 202px;
    background: var(--paper);
    box-shadow: 0 2px 6px rgba(0,0,0,0.12);
    overflow: hidden;
  }
  .slide--title { background: var(--navy); }
  .slide--hero { left: 143px; top: 110px; transform: scale(1.5); transform-origin: top left; }
  .slide--front { left: 33px; top: 582px; }
  .slide--p1 { left: 436px; top: 582px; }
  .slide--p2 { left: 33px; top: 831px; }
  .slide--p3 { left: 436px; top: 831px; }

  .page-label {
    position: absolute; width: 363px; text-align: center;
    font-size: 10px; font-weight: 600; letter-spacing: 1px; color: var(--ink);
  }

  .brand { position: absolute; display: flex; align-items: center; gap: 6px; }
  .brand__dot { border-radius: 50%; flex: none; }
  .brand__name { font-weight: 700; white-space: nowrap; }
  .brand--light { left: 14px; top: 14px; }
  .brand--light .brand__dot { width: 20px; height: 20px; background: var(--paper); }
  .brand--light .brand__name { color: var(--paper); font-size: 11px; }
  .brand--small { right: 14px; top: 12px; gap: 4px; }
  .brand--small .brand__dot { width: 10px; height: 10px; background: var(--navy); }
  .brand--small .brand__name { color: var(--navy); font-size: 6px; }

  .title-decor {
    position: absolute; right: 0; top: 0; width: 58px; height: 202px;
    background: linear-gradient(180deg, var(--navy) 0%, var(--navy-soft) 70%, #3a6a86 100%);
  }
  .title-kicker {
    position: absolute; left: 22px; top: 76px;
    font-size: 11px; letter-spacing: 1.5px; color: var(--gold); font-weight: 400;
  }
  .title-main {
    position: absolute; left: 20px; top: 90px;
    font-size: 29px; font-weight: 300; color: var(--paper); letter-spacing: 0.5px;
  }

  .heading { position: absolute; left: 20px; font-size: 15px; font-weight: 600; line-height: 1.15; }
  .heading .gold { color: var(--gold); }
  .heading .navy { color: var(--navy); }

  .bullets { position: absolute; left: 20px; top: 100px; list-style: none; }
  .bullets li { display: flex; align-items: center; gap: 6px; font-size: 5.5px; color: var(--muted); margin-bottom: 9px; }
  .bullets li::before {
    content: ""; width: 8px; height: 8px; border-radius: 50%;
    border: 1px solid var(--gold); flex: none;
  }
  .device-visual {
    position: absolute; left: 200px; top: 62px; width: 145px; height: 100px;
    background: linear-gradient(160deg, #dfe3e6, #9ea6ad);
    border-radius: 4px;
  }

  .about-text { position: absolute; left: 20px; top: 62px; width: 160px; font-size: 5.5px; line-height: 1.6; color: var(--muted); }
  .about-panel { position: absolute; right: 0; top: 0; width: 165px; height: 202px; background: var(--navy); padding: 22px 16px; }
  .steps { list-style: none; }
  .steps li { display: flex; align-items: center; gap: 7px; font-size: 5.5px; color: var(--paper); margin-bottom: 8px; }
  .steps__num {
    width: 11px; height: 11px; border-radius: 50%; border: 1px solid var(--gold);
    display: flex; align-items: center; justify-content: center; font-size: 5px; color: var(--gold); flex: none;
  }
  .about-panel p { font-size: 5.5px; line-height: 1.6; color: #c6d3dc; margin-top: 12px; }

  .stats { position: absolute; left: 20px; right: 20px; top: 68px; display: flex; justify-content: space-between; }
  .stat { width: 92px; text-align: center; }
  .stat svg { display: block; margin: 0 auto 8px; }
  .stat h3 { font-size: 6px; font-weight: 700; color: var(--navy); margin-bottom: 4px; }
  .stat p { font-size: 5px; line-height: 1.5; color: var(--muted); }

  .footer-rule { position: absolute; left: 20px; right: 20px; bottom: 10px; height: 1px; background: var(--line); }
  .page-num { position: absolute; right: 14px; bottom: 4px; font-size: 5px; color: var(--muted); }

  .brand--footer { left: 50%; top: 1115px; transform: translateX(-50%); gap: 10px; }
  .brand--footer .brand__dot { width: 38px; height: 38px; background: var(--navy); }
  .brand--footer .brand__name { color: var(--navy); font-size: 15px; }
</style>
</head>
<body>

  <section class="slide slide--title slide--hero">
    <div class="title-decor" role="img" aria-label="Decorative line motif area"></div>
    <div class="brand brand--light"><span class="brand__dot"></span><span class="brand__name">Kinetic Seven Economics</span></div>
    <p class="title-kicker">POWERPOINT</p>
    <h1 class="title-main">PRESENTATION</h1>
  </section>

  <section class="slide slide--title slide--front">
    <div class="title-decor" role="img" aria-label="Decorative line motif area"></div>
    <div class="brand brand--light"><span class="brand__dot"></span><span class="brand__name">Kinetic Seven Economics</span></div>
    <p class="title-kicker">POWERPOINT</p>
    <h2 class="title-main">PRESENTATION</h2>
  </section>
  <p class="page-label" style="left:33px; top:794px;">FRONT PAGE</p>

  <section class="slide slide--p1">
    <div class="brand brand--small"><span class="brand__dot"></span><span class="brand__name">Kinetic Seven Economics</span></div>
    <h2 class="heading" style="top:28px;"><span class="gold">LOREM</span><br><span class="navy">IPSUM SIMPLY</span><br><span class="navy">TEXT GOES HERE</span></h2>
    <ul class="bullets">
      <li>Lorem ipsum is simply dummy text</li>
      <li>Lorem ipsum is simply dummy text</li>
      <li>Lorem ipsum is simply dummy text</li>
      <li>Lorem ipsum is simply dummy text</li>
    </ul>
    <div class="device-visual" role="img" aria-label="Laptop showing a grid of service icons"></div>
    <div class="footer-rule"></div>
    <span class="page-num">01</span>
  </section>
  <p class="page-label" style="left:436px; top:794px;">PAGE - 01</p>

  <section class="slide slide--p2">
    <h2 class="heading" style="top:40px;"><span class="navy">ABOUT</span> <span class="gold">US</span></h2>
    <p class="about-text">Lorem ipsum is simply dummy text of the printing and typesetting industry. It has been the standard sample text since the early days, used to show layout and type before final copy arrives.</p>
    <div class="about-panel">
      <ol class="steps">
        <li><span class="steps__num">1</span>Lorem ipsum simply dummy text</li>
        <li><span class="steps__num">2</span>Lorem ipsum simply dummy text</li>
        <li><span class="steps__num">3</span>Lorem ipsum simply dummy text</li>
        <li><span class="steps__num">4</span>Lorem ipsum simply dummy text</li>
        <li><span class="steps__num">5</span>Lorem ipsum simply dummy text</li>
      </ol>
      <p>Lorem ipsum is simply dummy text of the printing and typesetting industry.</p>
    </div>
    <span class="page-num" style="right:175px;">02</span>
  </section>
  <p class="page-label" style="left:33px; top:1043px;">PAGE - 02</p>

  <section class="slide slide--p3">
    <div class="brand brand--small"><span class="brand__dot"></span><span class="brand__name">Kinetic Seven Economics</span></div>
    <h2 class="heading" style="top:28px;"><span class="gold">LOREM</span> <span class="navy">IPSUM</span></h2>
    <div class="stats">
      <div class="stat">
        <svg width="54" height="54" viewBox="0 0 54 54"><circle cx="27" cy="27" r="22" fill="none" stroke="#d9dee2" stroke-width="6"/><circle cx="27" cy="27" r="22" fill="none" stroke="#c9a063" stroke-width="6" stroke-dasharray="35 139" transform="rotate(-90 27 27)"/></svg>
        <h3>TEXT HERE</h3>
        <p>Lorem ipsum is simply dummy text of the printing industry</p>
      </div>
      <div class="stat">
        <svg width="54" height="54" viewBox="0 0 54 54"><circle cx="27" cy="27" r="22" fill="none" stroke="#d9dee2" stroke-width="6"/><circle cx="27" cy="27" r="22" fill="none" stroke="#c9a063" stroke-width="6" stroke-dasharray="35 139" transform="rotate(-90 27 27)"/></svg>
        <h3>TEXT HERE</h3>
        <p>Lorem ipsum is simply dummy text of the printing industry</p>
      </div>
      <div class="stat">
        <svg width="54" height="54" viewBox="0 0 54 54"><circle cx="27" cy="27" r="22" fill="none" stroke="#d9dee2" stroke-width="6"/><circle cx="27" cy="27" r="22" fill="none" stroke="#c9a063" stroke-width="6" stroke-dasharray="35 139" transform="rotate(-90 27 27)"/></svg>
        <h3>TEXT HERE</h3>
        <p>Lorem ipsum is simply dummy text of the printing industry</p>
      </div>
    </div>
    <div class="footer-rule"></div>
    <span class="page-num">03</span>
  </section>
  <p class="page-label" style="left:436px; top:1043px;">PAGE - 03</p>

  <div class="brand brand--footer"><span class="brand__dot"></span><span class="brand__name">Kinetic Seven Economics</span></div>

</body>
</html>
```